Varnik Holdings — Business Card Design Brief
Overview
Design a double-sided business card for Varnik Holdings that highlights our two service arms: Varnik Communications (telecommunications) and Varnik Energy (business energy solutions). The card should feel smart and stand out when handed to clients.

Objectives
Showcase our areas of specialty clearly.
Reflect the overall Varnik / Varnik Holdings brand while acknowledging both arms.
Explore using both logos (Communications + Energy) or one unified logo, depending on the design.

Deliverables
One double-sided business card design (front + back).

Content & Copy
Front (preferred): Logo: Varnik / Varnik Holdings
Descriptor: Business Communications | Business Energy
Back:My contact details and company details
Core products: Business Mobile • Telephony • Internet • Business Energy Solutions

Brand & Visual Direction
We have a group logo currently tailored more toward telecoms, plus a separate Varnik Energy logo.
Please explore layouts that use both logos or just one, whichever works best.
Color: I wouldn't mind seeing an option using our the Blue/Purple gradient from our website (varnik-example.co.uk), but also open to non-gradient approaches and other colours..

Overall look: Smart, modern, and distinctive.
Format & Print Specs
Double-sided business card format. (Use a standard size

Must-Haves
Front: Varnik wording or Varnik Holdings wording with atleast 1 logo also on front “Business Communications | Business Energy.”

Back: Contact + company details and core products.
A design that stands out while remaining professional.

Nice-to-Have Options
A gradient version using our site’s Blue/Purple gradient.
A non-gradient version.
A dual-logo treatment versus a single-logo treatment.

Thanks
Owen

```html
<!DOCTYPE html>
<html lang="en">
<head>
<meta charset="utf-8">
<title>Varnik Holdings — Business Card</title>
<link rel="stylesheet" href="https://fonts.googleapis.com/css2?family=Montserrat:wght@700;800&family=Arimo:wght@400&display=swap">
<style>
  :root {
    --page: #e9e9e9;
    --card-white: #ffffff;
    --navy: #1e1760;
    --band-green: #22a512;
    --band-blue: #1660d8;
    --ring-green: #5cc21c;
    --ring-blue: #1a6ee0;
    --text-dark: #2a2a2a;
    --white: #ffffff;
    --grad-top: #d8d400;
    --grad-bottom: #22a512;
  }
  * { box-sizing: border-box; margin: 0; padding: 0; }
  html, body { width: 1200px; height: 1200px; overflow: hidden; }
  body { background: var(--page); font-family: "Arimo", Arial, sans-serif; position: relative; }

  .card { position: absolute; left: 255px; width: 690px; height: 394px; overflow: hidden; }
  .card-front { top: 159px; background: var(--card-white); }
  .card-back { top: 653px; background: linear-gradient(180deg, var(--grad-top), var(--grad-bottom)); }

  .wordmark {
    position: absolute; right: 50px; top: 22px;
    font-family: "Montserrat", Arial, sans-serif; font-weight: 800;
    font-size: 52px; color: var(--navy); letter-spacing: 1px; text-transform: uppercase;
  }

  .band { position: absolute; left: 0; width: 496px; height: 100px; display: flex; align-items: center; white-space: nowrap; }
  .band-green { top: 101px; background: var(--band-green); }
  .band-blue { top: 233px; background: var(--band-blue); }
  .band-ring {
    position: absolute; width: 102px; height: 102px; border-radius: 50%;
    background: var(--card-white); border: 10px solid; left: 445px;
  }
  .ring-green { top: 100px; border-color: var(--ring-green); }
  .ring-blue { top: 232px; border-color: var(--ring-blue); }

  .band-col { padding-left: 42px; padding-right: 18px; }
  .band-divider { width: 1px; height: 52px; background: var(--white); flex: none; }
  .band-col-right { padding-left: 16px; color: var(--white); font-size: 15px; line-height: 20px; }

  .person-name { font-family: "Montserrat", Arial, sans-serif; font-weight: 700; font-size: 24px; color: var(--navy); line-height: 27px; }
  .person-role { color: var(--white); font-size: 15px; }
  .address { color: var(--white); font-size: 15px; line-height: 20px; }

  .phone-line { display: flex; align-items: center; gap: 8px; }
  .phone-line svg { width: 13px; height: 14px; fill: var(--white); }

  .products { position: absolute; left: 38px; top: 350px; font-size: 17px; color: var(--text-dark); white-space: nowrap; }

  .arm { position: absolute; top: 122px; width: 260px; text-align: center; color: var(--white); }
  .arm-comms { left: 76px; }
  .arm-energy { left: 352px; }
  .arm-ring { width: 118px; height: 118px; border-radius: 50%; border: 12px solid var(--white); margin: 0 auto; }
  .arm-label { margin-top: 34px; font-size: 17px; text-transform: uppercase; white-space: nowrap; }
  .back-divider { position: absolute; left: 345px; top: 115px; width: 2px; height: 165px; background: var(--white); }
</style>
</head>
<body>
  <section class="card card-front" aria-label="Card front">
    <div class="wordmark">Varnik</div>

    <div class="band band-green">
      <div class="band-col">
        <div class="person-name">MAREK HOLLIS</div>
        <div class="person-role">President</div>
      </div>
      <div class="band-divider"></div>
      <div class="band-col-right">
        <div class="phone-line">
          <svg viewBox="0 0 24 24" aria-hidden="true"><path d="M6.6 10.8a15.1 15.1 0 0 0 6.6 6.6l2.2-2.2a1 1 0 0 1 1-.25 11.4 11.4 0 0 0 3.6.57 1 1 0 0 1 1 1V20a1 1 0 0 1-1 1A17 17 0 0 1 3 4a1 1 0 0 1 1-1h3.5a1 1 0 0 1 1 1c0 1.25.2 2.45.57 3.57a1 1 0 0 1-.25 1z"/></svg>
          555-210-4871
        </div>
        <div class="phone-line">
          <svg viewBox="0 0 24 24" aria-hidden="true"><path d="M7 1h10a2 2 0 0 1 2 2v18a2 2 0 0 1-2 2H7a2 2 0 0 1-2-2V3a2 2 0 0 1 2-2zm0 3v15h10V4z"/></svg>
          555-390-6624
        </div>
      </div>
    </div>
    <div class="band-ring ring-green"></div>

    <div class="band band-blue">
      <div class="band-col address">42 Alder Crescent<br>Northfield, Canada 118</div>
      <div class="band-divider"></div>
      <div class="band-col-right">info@varnik-example.co.uk<br>www.varnik-example.co.uk</div>
    </div>
    <div class="band-ring ring-blue"></div>

    <div class="products">Business Mobile &nbsp;•&nbsp; Telephony &nbsp;•&nbsp; Internet &nbsp;•&nbsp; Business Energy Solutions</div>
  </section>

  <section class="card card-back" aria-label="Card back">
    <div class="arm arm-comms">
      <div class="arm-ring"></div>
      <div class="arm-label">Business Communications</div>
    </div>
    <div class="back-divider"></div>
    <div class="arm arm-energy">
      <div class="arm-ring"></div>
      <div class="arm-label">Business Energy</div>
    </div>
  </section>
</body>
</html>
```